Business Card & Letterhead Design

We a financial advice company based in Australia. We provide advice to wealthy farmers.

We are changing our business name FROM Brightvale Financial TO Tallowmere Wealth and we need a new letterhead and double sided business card design

Attached is designs from our previous branding (Brightvale Financial) as it includes all the details we require on the new Tallowmere Wealth business cards and letterhead.

Need extra days to review

```html
<!DOCTYPE html>
<html lang="en">
<head>
<meta charset="utf-8">
<title>Tallowmere Wealth – Stationery</title>
<link href="https://fonts.googleapis.com/css2?family=Poppins:wght@400;500;600&family=Roboto:wght@300;400&family=EB+Garamond:ital,wght@0,400;1,400&display=swap" rel="stylesheet">
<style>
:root{
  --bg:#e6e6e6;
  --paper:#f7f7f7;
  --ink:#2b2b2b;
  --ink-soft:#555;
  --ink-light:#6b6b6b;
  --dark-card:#474747;
  --on-dark:#e4e4e4;
  --faint:#e8e8e8;
}
*{margin:0;padding:0;box-sizing:border-box}
html,body{width:1200px;height:1027px;overflow:hidden;background:var(--bg)}
body{position:relative;font-family:"Poppins",sans-serif;color:var(--ink)}
.sheet{position:absolute;background:var(--paper);overflow:hidden}
.letterhead{left:486px;top:97px;width:581px;height:820px}
.card{left:140px;width:292px;height:167px}
.card-front{top:543px}
.card-back{top:750px;background:var(--dark-card)}
.abs{position:absolute}
.watermark{position:absolute;border:6px solid var(--faint);border-radius:50%}
.brand-ring{position:absolute;border:2px solid currentColor;border-radius:50%}
.brand-name{position:absolute;left:0;right:0;text-align:center;font-family:"Poppins",sans-serif;font-weight:400;letter-spacing:.5px;text-transform:uppercase}
.brand-tag{position:absolute;left:0;right:0;text-align:center;font-size:5.2px;letter-spacing:2.6px;text-transform:uppercase}
.salutation{left:56px;top:193px;font-family:"Roboto",sans-serif;font-size:14px;color:var(--ink-soft)}
.body-copy{left:56px;top:236px;width:470px;font-family:"Roboto",sans-serif;font-weight:300;font-size:7.6px;line-height:12.3px;color:var(--ink-light);text-align:justify}
.body-copy p{margin-bottom:12.3px}
.signoff{left:56px;top:518px;font-family:"Roboto",sans-serif;font-weight:300;font-size:7.6px;color:var(--ink-light)}
.signature{left:56px;top:540px;width:86px;height:55px;background:linear-gradient(120deg,#ececec,#dcdcdc);border-radius:3px}
.motto{position:absolute;left:0;right:0;text-align:center}
.motto .head{font-weight:600;font-size:8.6px;line-height:11px}
.motto .sub{font-style:italic;font-size:8px;line-height:10px;display:flex;justify-content:center;align-items:center;gap:3px}
.motto .sub::before,.motto .sub::after{content:"";width:10px;height:1px;background:var(--ink-soft)}
.footer-cols{left:0;right:0;top:713px;display:flex;justify-content:center;font-size:7.6px;line-height:9.3px;color:var(--ink-soft)}
.footer-cols .left{text-align:right;padding-right:7px;border-right:1px solid var(--ink-soft);width:226px}
.footer-cols .right{padding-left:7px;width:226px}
.footer-legal{left:0;right:0;top:773px;text-align:center;font-size:7.6px;line-height:9.6px;color:var(--ink-soft)}
.card-front .motto{top:33px}
.card-front .motto .head{font-size:7.4px;line-height:9px}
.card-front .motto .sub{font-size:6.4px;line-height:8px}
.person{right:164px;top:67px;text-align:right;color:var(--ink-soft);font-size:5.6px;line-height:7px}
.person .name{font-weight:600;font-size:8.8px;line-height:11px;color:var(--ink)}
.person .quals{font-size:5.8px;margin-bottom:2px}
.divider-v{left:136px;top:66px;width:1px;height:45px;background:var(--ink-soft)}
.contacts{left:145px;top:66px;font-size:5.8px;line-height:8px;color:var(--ink-soft);list-style:none}
.contacts li{display:flex;align-items:center;gap:4px}
.contacts svg,.addresses svg{width:5px;height:5px;fill:var(--ink-soft);flex:none}
.addresses{left:0;right:0;top:121px;font-size:5.8px;line-height:9px;color:var(--ink-soft);list-style:none;text-align:center}
.addresses li{display:flex;justify-content:center;align-items:center;gap:2px}
.card-back .brand-name{top:94px;font-size:14px;color:var(--on-dark)}
.card-back .brand-tag{top:110px;color:#8a8a8a}
.services{left:0;right:0;top:124px;text-align:center;font-family:"EB Garamond",serif;font-size:7.4px;color:var(--on-dark)}
.licence{left:0;right:0;top:137px;text-align:center;font-family:"EB Garamond",serif;font-style:italic;font-size:5.6px;line-height:9px;color:#d0d0d0}
.licence .rule{display:flex;justify-content:center;align-items:center;gap:4px}
.licence .rule::before,.licence .rule::after{content:"";width:50px;height:1px;background:#9a9a9a}
</style>
</head>
<body>

<section class="sheet letterhead">
  <div class="watermark" style="left:115px;top:196px;width:370px;height:370px"></div>
  <div class="brand-ring" style="left:262px;top:44px;width:44px;height:44px;color:var(--ink-soft)"></div>
  <div class="brand-name" style="top:89px;font-size:13px;color:var(--ink-soft)">Tallowmere Wealth</div>
  <div class="brand-tag" style="top:106px;color:var(--ink-light)">Strategic Financial Advice</div>

  <div class="abs salutation">Dear Mr. Hartley,</div>
  <div class="abs body-copy">
    <p>Lorem ipsum dolor sit amet, consectetur adipiscing elit. Donec orci purus, luctus vitae dignissim eu, iaculis sed purus. Vivamus faucibus, ipsum nec aliquet viverra, leo mauris condimentum ligula, sit amet sagittis enim ligula quis arcu. Nam egestas tortor id nisi porttitor mattis. In tortor ante, ultricies in suscipit a, tempus non massa. Vivamus et auctor mi. Fusce vel massa nulla. Phasellus nec eros mauris, et scelerisque orci.</p>
    <p>Donec malesuada orci vitae nulla accumsan porta a id massa. Quisque accumsan iaculis magna sit amet fringilla. Maecenas consequat, magna eget tincidunt semper, odio nibh rutrum mi, id feugiat ante nisi eu risus. Vestibulum nunc orci, rhoncus a placerat in, ultricies in mi. Cras mattis varius eros, vel fringilla nisi suscipit eget. Quisque scelerisque sagittis nulla at porttitor.</p>
    <p>Sed id augue vitae urna euismod commodo aliquet a quam. Pellentesque arcu velit, cursus et malesuada ut, consequat et diam. Nullam erat sem, rhoncus id ullamcorper vitae, rhoncus et arcu. In ultricies ultricies nulla, ut rutrum nisi iaculis at. Donec eu magna a metus ornare faucibus. Fusce aliquet faucibus ultricies. Morbi semper, est id tincidunt gravida, sem arcu adipiscing lacus, ac bibendum nulla leo eu purus. Quisque nec diam sed risus consectetur a ccumsan quis quis nibh. Vestibulum id purus lorem.</p>
    <p>It is a long established fact that a reader will be distracted by the readable content of a page when looking at its layout. The point of using Lorem Ipsum is that it has a more-or-less normal distribution of letters, as opposed to using 'Content here, content here', making it look like readable English. Many desktop publishing packages</p>
    <p>ada ut, consequat et diam. Nullam erat sem, rhoncus id ullamcorper vitae, rhoncus et arcu. In ultricies ultricies nulla, ut rutrum nisi iaculis at. Donec eu magna a metus ornare faucibus. Fusce aliquet faucibus ultricies. Morbi semper,</p>
  </div>
  <div class="abs signoff">Sincerely,</div>
  <div class="abs signature" role="img" aria-label="Handwritten signature of Sam Carver"></div>

  <div class="motto" style="top:681px">
    <div class="head">FINANCIAL PEACE OF MIND</div>
    <div class="sub">A referral built business</div>
  </div>
  <div class="abs footer-cols">
    <div class="left">Northgate Holdings Pty Ltd | ATF The Ashford Investment Trust T/AS Brightvale Financial | ABN: 12 345 678 901 Corporate Authorised Representative of Meridian Advice Group Limited</div>
    <div class="right">Suite 4A, 18 Carrow Lane, Riverton QLD 4101<br>PO Box 5120, Eastbank QLD 4102<br>p (07) 5550 1200 f (07) 5550 1299<br>admin@brightvalefinancial.com.au<br>www.brightvalefinancial.com.au</div>
  </div>
  <div class="abs footer-legal">Meridian Advice Group Limited | ABN 48 123 456 789 | Australian Financial Services Licence<br>Licence Number 100 200 | Principle Address: 410 Harbour Rd, PO Box 1180 Southport VIC 3000</div>
</section>

<section class="sheet card card-front">
  <div class="watermark" style="left:91px;top:33px;width:104px;height:104px;border-width:4px"></div>
  <div class="motto">
    <div class="head">FINANCIAL PEACE OF MIND</div>
    <div class="sub">A referral built business</div>
  </div>
  <div class="abs person">
    <div class="name">SAM CARVER</div>
    <div class="quals">B.Ag.Ec. Dip F.P. CFP®</div>
    <div>Managing Director</div>
    <div>Authorised Representative</div>
  </div>
  <div class="abs divider-v"></div>
  <ul class="abs contacts">
    <li><svg viewBox="0 0 10 10"><path d="M2 0l2 2.5-1.2 1.3a6 6 0 003.4 3.4L7.5 6 10 8l-1.5 2C4 10 0 6 0 1.5z"/></svg>(07) 5550 1200</li>
    <li><svg viewBox="0 0 10 10"><path d="M2.5 0h5v10h-5zM3.5 1v7h3V1z"/></svg>0400 555 218</li>
    <li><svg viewBox="0 0 10 10"><path d="M2 0h6v3H2zM0 3.5h10V8H8v2H2V8H0zM3 7v2h4V7z"/></svg>(07) 5550 1299</li>
    <li><svg viewBox="0 0 10 10"><path d="M0 2h10v1L5 6 0 3zM0 4l5 3 5-3v4H0z"/></svg>sam@brightvalefinancial.com.au</li>
    <li><svg viewBox="0 0 10 10"><circle cx="5" cy="5" r="4.5"/></svg>www.brightvalefinancial.com.au</li>
  </ul>
  <ul class="abs addresses">
    <li><svg viewBox="0 0 10 10"><path d="M5 0a3.5 3.5 0 013.5 3.5C8.5 6 5 10 5 10S1.5 6 1.5 3.5A3.5 3.5 0 015 0zm0 2a1.5 1.5 0 100 3 1.5 1.5 0 000-3z"/></svg>Suite 4A, 18 Carrow Lane, Riverton QLD 4101</li>
    <li><svg viewBox="0 0 10 10"><path d="M5 0a3.5 3.5 0 013.5 3.5C8.5 6 5 10 5 10S1.5 6 1.5 3.5A3.5 3.5 0 015 0zm0 2a1.5 1.5 0 100 3 1.5 1.5 0 000-3z"/></svg>PO Box 5120, Eastbank QLD 4102</li>
  </ul>
</section>

<section class="sheet card card-back">
  <div class="brand-ring" style="left:124px;top:42px;width:44px;height:44px;color:#2e2e2e"></div>
  <div class="brand-name">Tallowmere Wealth</div>
  <div class="brand-tag">Strategic Financial Advice</div>
  <div class="abs services">Life &amp; TPD Insurance • Income Protection • Financial Planning</div>
  <div class="abs licence">
    <div class="rule">Meridian Advice Group limited</div>
    <div>Australian Financial Services licensee License Number 100200</div>
  </div>
</section>

</body>
</html>
```